Bramblewood Card Company Business Cards

We are a trading card store with Glimmorax, sports and other TCG cards, we need a business card design that encompasses a clean cut, modern style with a retro flare. website is bramblewoodcardco.com for reference. Can utilize a comic book era feel or a more modern outdoor feel to utilize the "Pacific Northwest" elements of tress, mountains, etc.

Industry/Entity Type

Trading cards and collectibles

Contact Information for Business Card

business name, email address, phone number, name, owner job title

Font styles to use
Sans Serif

```html
<!DOCTYPE html>
<html lang="en">
<head>
<meta charset="utf-8">
<title>Bramblewood Card Company – Business Cards</title>
<link href="https://fonts.googleapis.com/css2?family=Montserrat:wght@600&family=Open+Sans:wght@400;700&display=swap" rel="stylesheet">
<style>
  :root {
    --backdrop: #3a3a3a;
    --card-white: #ffffff;
    --brand-cyan: #22bedf;
    --brand-grey: #6f6f6f;
    --ink: #1f1f1f;
  }
  * { box-sizing: border-box; margin: 0; padding: 0; }
  html, body {
    width: 1200px; height: 1059px; overflow: hidden;
    background: var(--backdrop);
    font-family: "Open Sans", sans-serif;
  }
  .canvas { position: relative; width: 1200px; height: 1059px; }

  .card {
    position: absolute;
    border-radius: 24px;
    overflow: hidden;
    box-shadow: 0 14px 28px rgba(0,0,0,0.45);
  }
  .card-front { left: 256px; top: 100px; width: 688px; height: 391px; background: var(--card-white); }
  .card-back  { left: 253px; top: 537px; width: 694px; height: 394px; background: var(--brand-cyan); }

  .brand-name {
    position: absolute;
    display: flex; align-items: center; gap: 10px;
    font-family: "Open Sans", sans-serif;
    font-weight: 700;
    letter-spacing: 1px;
    line-height: 1.15;
    text-transform: uppercase;
  }
  .brand-mark { flex: none; width: 16px; height: 16px; background: currentColor; }
  .card-front .brand-name { left: 31px; top: 78px; font-size: 18px; color: var(--brand-grey); }
  .card-back .brand-name {
    left: 0; right: 0; top: 160px; justify-content: center;
    font-size: 34px; color: var(--brand-grey);
  }
  .card-back .brand-mark { width: 26px; height: 26px; }

  .holder-name {
    position: absolute; right: 31px; top: 168px;
    font-family: "Montserrat", sans-serif; font-weight: 600;
    font-size: 31px; line-height: 38px; letter-spacing: 1px;
    color: var(--brand-cyan);
  }
  .holder-title {
    position: absolute; right: 31px; top: 202px;
    font-size: 16px; line-height: 20px; color: var(--ink);
  }
  .rule { position: absolute; left: 31px; top: 212px; width: 521px; height: 2px; background: var(--brand-cyan); }
  .side-tab {
    position: absolute; right: 0; top: 176px; width: 16px; height: 38px;
    background: var(--brand-cyan); border-radius: 4px 0 0 4px;
  }

  .address {
    position: absolute; left: 31px; top: 250px;
    font-size: 16px; line-height: 20px; color: var(--ink); font-style: normal;
  }
  .contacts { position: absolute; left: 31px; top: 298px; list-style: none; }
  .contacts li {
    display: flex; align-items: center; gap: 7px;
    font-size: 16px; line-height: 21px; color: var(--ink);
  }
  .contacts svg { width: 11px; height: 11px; fill: var(--brand-cyan); flex: none; }
</style>
</head>
<body>
<div class="canvas">

  <section class="card card-front" aria-label="Business card front">
    <div class="brand-name"><span class="brand-mark"></span><span>Bramblewood<br>Card Company</span></div>

    <h1 class="holder-name">DALEN CARVER</h1>
    <p class="holder-title">MANAGER</p>
    <div class="rule"></div>
    <div class="side-tab"></div>

    <address class="address">4185 Larchmont Avenue South<br>Kentwood, WA 98031 USA</address>

    <ul class="contacts">
      <li>
        <svg viewBox="0 0 12 12" aria-hidden="true"><path d="M2.4 0.8l1.8 0 0.9 2.6-1.2 1c0.7 1.5 1.7 2.5 3.1 3.2l1-1.2 2.6 0.9v1.8c0 0.6-0.5 1.1-1.1 1.1C4.6 10.2 1.3 6.9 1.3 1.9c0-0.6 0.5-1.1 1.1-1.1z"/></svg>
        555-3814-2270
      </li>
      <li>
        <svg viewBox="0 0 12 12" aria-hidden="true"><path d="M0 2.5h12v7H0z M0.8 3.2L6 6.8l5.2-3.6" stroke="#fff" stroke-width="0.8"/></svg>
        hello@bramblewoodcardco.com
      </li>
      <li>
        <svg viewBox="0 0 12 12" aria-hidden="true"><circle cx="6" cy="6" r="5.5"/><path d="M3 3.5c1 0 1.5 1 2.5 1s0.5 2-0.8 2.2M7 8.5c0.5-1 2-1 2.5-2" stroke="#fff" stroke-width="0.9" fill="none"/></svg>
        www.bramblewoodcardco.com
      </li>
    </ul>
  </section>

  <section class="card card-back" aria-label="Business card back">
    <div class="brand-name"><span class="brand-mark"></span><span>Bramblewood<br>Card Company</span></div>
  </section>

</div>
</body>
</html>
```